RB Halden Electric Yard Sign

Looking to have a yard sign designed that we can place at projects we are working on. Most likely will be 18" H x 24" W but flexible that we can increase the size if necessary. It should include our logo, our phone # 609-555-0147, website rbhaldenelectric.example and slogan, built on integrity, driven by excellence. Colors should match our brand.

```html
<!DOCTYPE html>
<html lang="en">
<head>
<meta charset="utf-8">
<title>RB Halden Electric Yard Sign</title>
<link href="https://fonts.googleapis.com/css2?family=Archivo:wdth,wght@100..125,700..900&family=Oswald:wght@500&display=swap" rel="stylesheet">
<style>
  :root {
    --backdrop: #4f4f4f;
    --sign-white: #ffffff;
    --navy: #06365a;
    --red: #e0202a;
  }
  * { margin: 0; padding: 0; box-sizing: border-box; }
  html, body {
    width: 1200px; height: 1001px; overflow: hidden;
    background: var(--backdrop);
  }
  .yard-sign {
    position: absolute; left: 151px; top: 164px;
    width: 897px; height: 672px;
    background: var(--sign-white);
    overflow: hidden;
  }
  .sign-bands { position: absolute; inset: 0; width: 100%; height: 100%; }
  .brand-block {
    position: absolute; left: 0; right: 0; top: 50px; height: 210px;
    display: flex; flex-direction: column; justify-content: center; align-items: center; gap: 22px;
  }
  .brand-dot { width: 74px; height: 74px; border-radius: 50%; background: var(--red); flex: none; }
  .brand-name {
    font-family: "Archivo", sans-serif; font-weight: 900; font-stretch: 125%;
    font-size: 64px; line-height: 1; color: var(--navy); letter-spacing: 1px; white-space: nowrap;
  }
  .contact-line {
    position: absolute; left: 73px; right: 40px;
    display: flex; align-items: center; gap: 10px;
    font-family: "Archivo", sans-serif; font-stretch: 125%; color: var(--navy);
  }
  .contact-phone { top: 310px; height: 70px; font-size: 70px; font-weight: 900; letter-spacing: 15px; }
  .contact-web { top: 402px; height: 40px; font-size: 36px; font-weight: 900; letter-spacing: 3px; gap: 12px; }
  .contact-icon { flex: none; fill: var(--red); }
  .contact-text { line-height: 1; white-space: nowrap; }
  .slogan {
    position: absolute; left: 0; right: 0; top: 484px; height: 70px;
    display: flex; align-items: center; justify-content: center;
    font-family: "Oswald", sans-serif; font-weight: 500; font-style: italic;
    font-variant: small-caps; font-size: 52px; color: var(--sign-white);
    letter-spacing: -0.5px; white-space: nowrap;
  }
</style>
</head>
<body>
  <main class="yard-sign">
    <svg class="sign-bands" viewBox="0 0 1121 840" preserveAspectRatio="none" aria-hidden="true">
      <polygon fill="var(--navy)" points="0,580 1121,580 1121,717 247,717 0,675"/>
      <polygon fill="var(--navy)" points="0,687 901,840 0,840"/>
      <polygon fill="var(--red)" points="649,788 1121,727 1121,840 941,840"/>
    </svg>

    <div class="brand-block">
      <span class="brand-dot"></span>
      <span class="brand-name">RB Halden Electric</span>
    </div>

    <div class="contact-line contact-phone">
      <svg class="contact-icon" width="30" height="38" viewBox="0 0 24 30" aria-label="Phone">
        <path d="M6 1 L10 8 L7 11 C8 16 10 19 13 22 L16 20 L21 25 L18 29 C10 28 2 18 2 6 Z"/>
      </svg>
      <span class="contact-text">609-555-0147</span>
    </div>

    <div class="contact-line contact-web">
      <svg class="contact-icon" width="30" height="30" viewBox="0 0 30 30" aria-label="Website">
        <circle cx="15" cy="15" r="13" fill="none" stroke="var(--red)" stroke-width="3"/>
        <ellipse cx="15" cy="15" rx="6" ry="13" fill="none" stroke="var(--red)" stroke-width="2"/>
        <line x1="2" y1="15" x2="28" y2="15" stroke="var(--red)" stroke-width="2"/>
        <line x1="4" y1="9" x2="26" y2="9" stroke="var(--red)" stroke-width="2"/>
        <line x1="4" y1="21" x2="26" y2="21" stroke="var(--red)" stroke-width="2"/>
        <line x1="15" y1="2" x2="15" y2="28" stroke="var(--red)" stroke-width="2"/>
      </svg>
      <span class="contact-text">RBHALDENELECTRIC.EXAMPLE</span>
    </div>

    <p class="slogan">Built On Integrity, Driven By Excellence</p>
  </main>
</body>
</html>
```